KORV PTY LTD - Business Cards

Design a modern business card - using the attached Designs.
Same design as on the front, apart from the names/numbers/emails to be different.
We want the cards to be very glossy to stand out, do I think the simple black/white/metallic will be effective.
Both lots of details below:

Tom Wrenshaw
Director
tom_korv@nulvane.com
0438 274 093

Lewis Corbyn
Director
lewis_korv@nulvane.com
0419 385 642

Industry/Entity Type

Business

```html
<!DOCTYPE html>
<html lang="en">
<head>
<meta charset="utf-8">
<title>KORV PTY LTD – Business Cards</title>
<link href="https://fonts.googleapis.com/css2?family=Bitter:wght@400;600&display=swap" rel="stylesheet">
<style>
  :root {
    --canvas: #e9e9e9;
    --card-white: #ffffff;
    --ink: #2b2b2b;
    --ink-soft: #3a3a3a;
    --rule: #c9c9c9;
    --band-light: #d4d6d8;
    --band-dark: #3d4245;
    --back-black: #000000;
    --back-glow: #b9b9b9;
    --brand-steel: #4a5458;
    --brand-light: #e6e8e9;
  }
  * { margin: 0; padding: 0; box-sizing: border-box; }
  html, body {
    width: 1200px; height: 457px; overflow: hidden;
    background: var(--canvas);
    font-family: "Bitter", Georgia, serif;
  }
  .sheet {
    position: relative; width: 1200px; height: 457px;
    display: flex; justify-content: center; align-items: center; gap: 60px;
  }
  .card {
    position: relative; width: 540px; height: 320px; overflow: hidden;
    box-shadow: 0 6px 18px rgba(0,0,0,.25);
  }
  .card--front { background: var(--card-white); }
  .card--back {
    background: radial-gradient(ellipse 46% 62% at 50% 50%, var(--back-glow) 0%, #6a6a6a 40%, #1e1e1e 75%, var(--back-black) 100%);
  }
  .brand {
    position: absolute; left: 50%; transform: translateX(-50%);
    display: flex; align-items: center; gap: 12px;
    font-weight: 600; white-space: nowrap; letter-spacing: .06em;
  }
  .card--front .brand { top: 64px; font-size: 30px; color: var(--brand-steel); }
  .card--back .brand { top: 50%; transform: translate(-50%, -50%); font-size: 40px; color: var(--brand-light); }
  .brand__dot { border-radius: 50%; background: currentColor; flex: none; }
  .card--front .brand__dot { width: 22px; height: 22px; }
  .card--back .brand__dot { width: 30px; height: 30px; }

  .contact {
    position: absolute; left: 0; right: 0; top: 212px;
    display: flex; justify-content: center; align-items: stretch;
  }
  .contact__person { text-align: right; padding: 16px 16px 0 0; border-right: 1px solid var(--rule); }
  .contact__name { font-size: 17px; color: var(--ink); }
  .contact__role { font-size: 12px; color: var(--ink-soft); margin-top: 6px; }
  .contact__details { list-style: none; padding-left: 16px; font-size: 15px; color: var(--ink); }
  .contact__details li { display: flex; align-items: center; gap: 6px; height: 24px; }
  .contact__details svg { width: 12px; height: 12px; fill: var(--ink); }

  .band-light { position: absolute; left: 0; right: 0; bottom: 12px; height: 6px; background: var(--band-light); }
  .band-dark { position: absolute; left: 0; right: 0; bottom: 0; height: 12px; background: var(--band-dark); }
</style>
</head>
<body>
<main class="sheet">
  <section class="card card--front" aria-label="Card front">
    <div class="brand"><span class="brand__dot"></span>KORV PTY LTD</div>
    <div class="contact">
      <div class="contact__person">
        <p class="contact__name">Lewis Corbyn</p>
        <p class="contact__role">Director</p>
      </div>
      <ul class="contact__details">
        <li>
          <svg viewBox="0 0 12 12" aria-hidden="true"><path d="M2.5 1l2 2.3-1 1.2c.6 1.4 1.6 2.4 3 3l1.2-1 2.3 2-1.3 2C5 10.3 1.7 7 1 3.3z"/></svg>
          0419 385 642
        </li>
        <li>
          <svg viewBox="0 0 12 12" aria-hidden="true"><path d="M1 3h10v7H1z M1 3l5 4 5-4" fill="none" stroke="#2b2b2b" stroke-width="1.4"/></svg>
          lewis_korv@nulvane.com
        </li>
      </ul>
    </div>
    <div class="band-light"></div>
    <div class="band-dark"></div>
  </section>

  <section class="card card--back" aria-label="Card back">
    <div class="brand"><span class="brand__dot"></span>KORV PTY LTD</div>
  </section>
</main>
</body>
</html>
```